Leading Financial Advisory Firm Needs a Web Redesign

Job Type
Web Redesign

Task Outline
Create an Updated Web Design for our existing web site

Task Description
Dunmore Kestrel Group Inc. is a leading financial advisory firm to the global steel, metals and mining sectors. We are seeking a web designer to refashion, freshen and update the look of our existing website. The substance of the revised website should reflect our updated Credentials attached.

Our existing web site has an outdated “look”; it was originally put together quickly from an earlier PowerPoint presentation of our Credentials. We do not want the revised web site to look like a PowerPoint presentation which has been put up online. Rather, with a designer’s help, we would like to refashion the pages so that the look and feel of the site is consistent with a professional service organization's site. We are not interested in any significant changes in substance, just in format. There should also be no changes to the design/font/color of the “Dunmore Kestrel” logo.

The final selected designer will be responsible for all design and coding/programming responsibilities subject to our approval. The revised site should be done in Word Press or similar "user-friendly" application so that we can make edits afterwards.

A few specific changes:
• Textual changes:
• Wherever it currently says Dunmore Kestrel is an “affiliate” of Orvanne, this should be replaced with “Broker Dealer related services provided through Orvanne Partners LLC”; this appears on the copyright info on the bottom of each page;
• Please also add this telephone number to the 212 number listed: 917-555-0183;
• The text on the “About Us” tab needs to be updated as follows: “We currently have active steel, metals and mining assignments in Europe, South Africa, Australia and Ukraine.”
• The Services tab under Core Services currently says “Capital Raising (through affiliates)”; it should say “Capital Raising (through broker dealers)”;
• Our firm name in the Contacts tab should be “Dunmore Kestrel Group Inc.”
• Tara Wendle’ bio should be removed from the Bios tab;
• The map in the Global Scope and Perspective tab should be replaced with the map in the attached updated Credentials (see slide 11)

Very truly yours,

Dunmore Kestrel Group Inc.

Our current website is: http://www.dunmorekestrel.example

Deadline
5 Days

Target Market(s)
Companies in the steel, metals and mining sectors interested in financial advisory services and/or strategic and/or financial partners.

Industry/Entity Type

Financial

```html
<!DOCTYPE html>
<html lang="en">
<head>
<meta charset="utf-8">
<title>Dunmore Kestrel — Financial Advisory</title>
<link rel="stylesheet" href="https://fonts.googleapis.com/css2?family=Open+Sans:wght@300;400;600;700&family=Arimo:wght@400&display=swap">
<style>
  :root {
    --green: #137a1f;
    --green-dark: #0d6a18;
    --green-light: #2b9a38;
    --heading: #1d6f22;
    --text: #6f6f6f;
    --text-dark: #222;
    --footer: #333333;
    --white: #ffffff;
    --rule: #cfcfcf;
    --fb: #3b5ba4;
    --tw: #2fa5dc;
    --rss: #f27a1c;
    --yt: #d32a25;
  }
  * { box-sizing: border-box; margin: 0; padding: 0; }
  html, body { width: 883px; height: 1200px; overflow: hidden; background: var(--white); }
  body { position: relative; font-family: "Open Sans", Arial, sans-serif; color: var(--text); }
  .abs { position: absolute; }

  /* header */
  .brand-name { left: 64px; top: 46px; font-size: 23px; font-weight: 600; color: var(--green); letter-spacing: 1px; text-transform: uppercase; }
  .call { right: 99px; top: 40px; text-align: right; }
  .call-label { font-size: 14px; color: #777; font-weight: 300; }
  .call-number { font-size: 19px; color: var(--green); line-height: 1.2; }
  .call-icon { left: 794px; top: 48px; }

  /* nav */
  .nav { left: 64px; top: 103px; width: 755px; height: 43px; background: var(--green); display: flex; }
  .nav a { display: flex; align-items: center; justify-content: center; height: 100%; color: var(--white); text-decoration: none; font-size: 11.5px; font-weight: 600; border-right: 1px solid var(--green-dark); }
  .nav a:last-child { border-right: 0; }
  .nav a.active { background: var(--green-light); }

  /* hero */
  .hero { left: 64px; top: 146px; width: 755px; height: 314px; background: radial-gradient(ellipse at 48% 45%, #8a5a2a 0%, #4a3a2c 30%, #262423 65%, #1a1a1a 100%); }
  .hero-title { left: 108px; top: 328px; font-size: 27px; color: var(--white); letter-spacing: -0.5px; }
  .hero-sub { left: 109px; top: 367px; font-size: 14px; font-weight: 600; color: var(--white); }
  .dots { left: 727px; top: 439px; display: flex; gap: 8px; }
  .dots span { width: 12px; height: 12px; border-radius: 50%; background: #8a8a8a; border: 1px solid #bbb; }

  /* services */
  .card { width: 228px; }
  .card-frame { width: 228px; height: 121px; border: 1px solid #ddd; box-shadow: 0 1px 3px rgba(0,0,0,.15); padding: 5px; background: var(--white); }
  .card-frame div { width: 100%; height: 100%; }
  .card h2 { margin-top: 8px; font-size: 17.5px; font-weight: 400; color: var(--heading); }
  .card p { margin-top: 3px; font-size: 10.5px; line-height: 21.2px; color: var(--text); white-space: nowrap; }
  .card .more { display: block; font-size: 11.5px; line-height: 21px; color: #666; }

  /* featured */
  .section-title { font-size: 19.5px; font-weight: 400; color: var(--heading); }
  .article { width: 200px; }
  .article-img { width: 194px; height: 112px; }
  .article h3 { margin-top: 12px; font-size: 14.5px; font-weight: 400; color: var(--text-dark); }
  .article p { margin-top: 5px; font-size: 10.5px; line-height: 18.5px; color: var(--text); font-weight: 300; white-space: nowrap; }
  .article .read { display: block; width: 194px; text-align: right; margin-top: 6px; font-size: 11px; color: var(--green); }

  /* events */
  .event { left: 581px; width: 232px; }
  .event h4 { font-family: "Arimo", Arial, sans-serif; font-size: 10.8px; font-weight: 400; color: var(--green-dark); }
  .event .date { margin-top: 13px; font-family: "Arimo", Arial, sans-serif; font-size: 10px; color: #777; }
  .event p { margin-top: 8px; font-size: 10.5px; line-height: 18.5px; color: var(--text); white-space: nowrap; }
  .divider { left: 581px; top: 953px; width: 232px; border-top: 1px dotted var(--rule); }

  /* footer */
  .footer { left: 0; top: 1112px; width: 883px; height: 88px; background: var(--footer); }
  .footer-links { left: 79px; top: 1135px; font-family: "Arimo", Arial, sans-serif; font-size: 10.8px; color: var(--white); }
  .copyright { left: 79px; top: 1161px; font-family: "Arimo", Arial, sans-serif; font-size: 10.8px; color: var(--white); }
  .social { left: 665px; top: 1144px; display: flex; gap: 10px; }
  .social span { width: 26.5px; height: 26.5px; display: block; }
</style>
</head>
<body>
  <header>
    <div class="abs brand-name">Dunmore Kestrel</div>
    <div class="abs call">
      <div class="call-label">Call today</div>
      <div class="call-number">917-555-0183</div>
    </div>
    <svg class="abs call-icon" width="26" height="30" viewBox="0 0 24 24" aria-hidden="true">
      <path fill="#137a1f" d="M6.6 2.2c.6-.4 1.4-.2 1.8.4l2 3.3c.3.6.2 1.3-.3 1.7l-1.5 1.2c.9 2.4 2.5 4.6 4.5 6.3l1.6-1.1c.5-.4 1.3-.3 1.7.2l2.4 3c.4.5.4 1.3-.1 1.8l-1.6 1.6c-1 1-2.6 1.3-3.9.6C8.1 18.6 4.8 14.3 3.5 9.3c-.4-1.5.1-3 1.2-4l1.9-3.1z"/>
    </svg>
  </header>

  <nav class="abs nav">
    <a class="active" style="width:73px">HOME</a>
    <a style="width:91px">ABOUT US</a>
    <a style="width:90px">SERVICES</a>
    <a style="width:223px">REPRESENTATIVE ENGAGEMENTS</a>
    <a style="width:212px">GLOBAL SCOPE &amp; PERSPECTIVE</a>
    <a style="width:66px">BIOS</a>
  </nav>

  <section>
    <div class="abs hero" role="img" aria-label="Photo of a steel worker in a hard hat amid grinding sparks"></div>
    <div class="abs hero-title">Duis autem vel eum iriure dolor in hendrerit</div>
    <div class="abs hero-sub">Typi non habent claritatem insitam; est usus legentis in iis qui facit</div>
    <div class="abs dots"><span></span><span></span><span></span><span></span></div>
  </section>

  <section>
    <div class="abs card" style="left:64px; top:499px;">
      <div class="card-frame"><div role="img" aria-label="Photo of a desk with a planning sketch and coffee mug" style="background:linear-gradient(135deg,#3c4f8a,#c8d0e6 55%,#2e3c6a)"></div></div>
      <h2>Strategic Advice</h2>
      <p>Lorem ipsum dolor sit amet consectetuer adi<br>piscing elit Nam cursus Morbi ut mi. Nullam e<br>nim leo Claritas est etiam processus dynam</p>
      <span class="more">Read More</span>
    </div>
    <div class="abs card" style="left:328px; top:499px;">
      <div class="card-frame"><div role="img" aria-label="Photo of two hands joining puzzle pieces" style="background:linear-gradient(135deg,#7bbbd0,#a6d3e0 50%,#5ea6bf)"></div></div>
      <h2>Mergers &amp; Acquisitions</h2>
      <p>Lorem ipsum dolor sit amet consectetuer adi<br>piscing elit Nam cursus Morbi ut mi. Nullam e<br>nim leo Claritas est etiam processus dynam</p>
      <span class="more">Read More</span>
    </div>
    <div class="abs card" style="left:592px; top:499px;">
      <div class="card-frame"><div role="img" aria-label="Photo of smiling business people in an office" style="background:linear-gradient(90deg,#c9b5a4,#dde6ee 50%,#3a3f4a)"></div></div>
      <h2>Anchor Investors</h2>
      <p>Lorem ipsum dolor sit amet consectetuer adi<br>piscing elit Nam cursus Morbi ut mi. Nullam e<br>nim leo Claritas est etiam processus dynam</p>
      <span class="more">Read More</span>
    </div>
  </section>

  <section>
    <h2 class="abs section-title" style="left:64px; top:796px;">Featured Article</h2>
    <div class="abs article" style="left:64px; top:841px;">
      <div class="article-img" role="img" aria-label="Photo of a glass and steel building roof" style="background:linear-gradient(160deg,#d9ecf7,#5fa6d4 60%,#2d6ea6)"></div>
      <h3>Made in the midlands tackles</h3>
      <p>Lasodiaer leroas accntium reuekentie rias<br>esa Inveveritati etchcto beatae vitae dicti<br>untaxplic versa. Nemo ispernadit aut.</p>
      <span class="read">Read full Article</span>
    </div>
    <div class="abs article" style="left:306px; top:841px;">
      <div class="article-img" role="img" aria-label="Photo of a metal grinder throwing sparks" style="background:radial-gradient(ellipse at 60% 60%,#c98a4a,#3a2e26 55%,#1c1c1c)"></div>
      <h3>Made in the midlands tackles</h3>
      <p>Lasodiaer leroas accntium reuekentie rias<br>esa Inveveritati etchcto beatae vitae dicti<br>untaxplic versa. Nemo ispernadit aut.</p>
      <span class="read">Read full Article</span>
    </div>
  </section>

  <aside>
    <h2 class="abs section-title" style="left:578px; top:797px;">Upcoming Events</h2>
    <div class="abs event" style="top:838px;">
      <h4>TYPI NON HABENT CLARITATEM INSITAM;</h4>
      <div class="date">26/11/2013</div>
      <p>Typi non habent claritatem insitam; est usislegen<br>tis in iis qui facit eorum claritatem Investigatnes.<br>Aptent taciti sociosqu litora torquente</p>
    </div>
    <div class="abs divider"></div>
    <div class="abs event" style="top:970px;">
      <h4>TYPI NON HABENT CLARITATEM INSITAM;</h4>
      <div class="date">26/11/2013</div>
      <p>Typi non habent claritatem insitam; est usislegen<br>tis in iis qui facit eorum claritatem Investigatnes.<br>Aptent taciti sociosqu litora torquente</p>
    </div>
  </aside>

  <footer>
    <div class="abs footer"></div>
    <div class="abs footer-links">Terms and Conditions | Privacy Promise | FAQ's | Contact Us</div>
    <div class="abs copyright">Copyright © 2013. All Rights Reserved.</div>
    <div class="abs social" aria-label="Social links">
      <span style="background:var(--fb)"></span>
      <span style="background:var(--tw)"></span>
      <span style="background:var(--rss)"></span>
      <span style="background:var(--yt)"></span>
    </div>
  </footer>
</body>
</html>
```